Orvane Thinner Logo and Packaging Design

We are seeking a striking and professional logo and packaging design for our new product line, Orvane Thinner. This logo will be used on the packaging for three different sizes of half-transparent carboys: 1L, 4L, and 20L. Orvane Thinner is a high-quality solvent brand known for its excellent solvency, fast-drying properties, and pleasant smell. The logo should feature an eagle motif to symbolize power and precision, and our slogan, "SOAR WITH PURPOSE." The design should be suitable for placement on hardware store and warehouse shelves. Additionally, we need the designer to create an eagle logo to accompany the packaging.

Packaging Dimensions:
1L Carboy:
Front: 71mm height x 142mm width
Side: 71mm height x 73mm width
4L Carboy:
Front: 160mm height x 170mm width
Side: 160mm height x 120mm width
20L Carboy:
Front: 245mm height x 190mm width
Side: 215mm height x 190mm width
Front Label Requirements:

Product Name: Thinner QXR
Volume: 20L
Precautionary Statements:
Keep Away from Sources of ignition - No Smoking
Avoid Contact with Eyes
Do Not Empty into Drains or Sewers
Take Precautionary Measures Against Static Discharge
Hazard Statements:
Flammable Liquid and Vapor
May be fatal if swallowed or enters Airways
Causes Skin Irritation
Causes Serious Eye Irritation
Causes Damage to Organs if Prolonged or Repeated Exposure
Hazard Pictograms: (Include relevant hazard symbols)
Design Requirements:

Logo: Eagle motif (to be designed by the designer)
Slogan: SOAR WITH PURPOSE
Color Scheme: Designer to recommend (should be striking and professional for retail display)

Please see my latest picture. Kindly note the packaging is in Plastic Carboy (not in metal tin as per PS).

Eagle to be more majestic and bigger (as if soaring in the sky).
Singapore landscape as background to have Singapore identity such as KTR, Corvale wheel, terrace at the cove etc.

Eagle to be more majestic and bigger, wings to spread wide.
We not want it to be of photo style, but more on a cartoon style. Please see my latest file uploaded.

Target Market(s)

Our target market includes painting companies, construction companies, direct household consumers, and industrial users who require high-quality solvents for various applications.

Industry/Entity Type

Chemical, spray paint and painting, household, industrial

Requirements
Must have
• Professional and Striking Design: Eye-catching and professional packaging for retail shelves. Eagle Logo: A strong, precise eagle logo. Slogan: "SOAR WITH PURPOSE" prominently displayed. Clear Precautionary and Hazard Statements: Important safety information and pictograms. Volume Indication: Clearly marked (e.g., 1L, 4L, 20L). Eagle to be more majestic and bigger (as if soaring in the sky). Singapore landscape as background to have Singapore identity such as KTR, Corvale wheel, terrace at the cove etc.
Nice to have
• Color Scheme Recommendations: Suggestions for a professional, striking color scheme. Versatility: Design elements adaptable across different sizes of packaging. Environmentally Friendly Elements: Indications of sustainability or eco-friendliness in the design.
Should not have
• Overly Complex Designs: Avoid cluttered or overly intricate designs that detract from readability. Inconsistent Branding: Ensure all elements are cohesive and align with the brand identity.

```html
<!DOCTYPE html>
<html lang="en">
<head>
<meta charset="utf-8">
<title>Orvane Thinner – Thinner QXR 4L Label</title>
<link rel="stylesheet" href="https://fonts.googleapis.com/css2?family=Montserrat:ital,wght@0,600;0,900;1,500&family=Arimo:wght@400;700&display=swap">
<style>
  :root {
    --stage: #707070;
    --navy: #1d1f57;
    --navy-soft: #2c3a7a;
    --red: #a92126;
    --red-deep: #8e1a1f;
    --white: #ffffff;
    --ink: #111111;
  }
  * { margin: 0; padding: 0; box-sizing: border-box; }
  html, body {
    width: 1200px; height: 840px; overflow: hidden;
    background: var(--stage);
  }
  .label {
    position: absolute; left: 200px; top: 30px;
    width: 800px; height: 780px;
    border-radius: 20px; overflow: hidden;
    background: var(--navy);
    color: var(--white);
  }
  .label-art { position: absolute; inset: 0; width: 800px; height: 780px; }
  .brand {
    position: absolute; left: 222px; top: 30px;
    display: flex; align-items: center; gap: 16px;
  }
  .brand-mark {
    width: 100px; height: 100px; border-radius: 50%;
    background: var(--white);
  }
  .brand-name {
    font-family: "Montserrat", sans-serif; font-weight: 600;
    font-size: 50px; line-height: 48px; letter-spacing: -0.5px;
    color: var(--white); text-transform: uppercase;
  }
  .slogan {
    position: absolute; left: 0; width: 800px; top: 150px;
    text-align: center;
    font-family: "Montserrat", sans-serif; font-style: italic; font-weight: 500;
    font-size: 31px; letter-spacing: 2px;
  }
  .product-name {
    position: absolute; left: 0; width: 800px; top: 226px;
    text-align: center;
    font-family: "Montserrat", sans-serif; font-weight: 900;
    font-size: 98px; line-height: 86px; letter-spacing: 1px;
    text-transform: uppercase;
  }
  .safety {
    position: absolute; left: 48px; top: 545px;
    font-family: "Arimo", sans-serif; font-size: 14.5px; line-height: 16.8px;
  }
  .safety-group + .safety-group { margin-top: 16px; }
  .safety-title { font-weight: 700; text-transform: uppercase; }
  .safety-item { display: flex; }
  .safety-item .num { width: 24px; flex: none; }
  .signal-word {
    position: absolute; left: 596px; top: 734px; width: 140px;
    text-align: center;
    font-family: "Arimo", sans-serif; font-weight: 700; font-size: 23px;
  }
  .volume {
    position: absolute; left: 593px; top: 425px; width: 132px;
    text-align: center;
    font-family: "Montserrat", sans-serif; font-weight: 900; font-size: 62px;
    color: var(--white);
  }
</style>
</head>
<body>
<main class="label">
  <svg class="label-art" viewBox="0 0 800 780">
    <defs>
      <radialGradient id="wing-glow" cx="0.3" cy="0.4" r="0.6">
        <stop offset="0" stop-color="#2c3a7a" stop-opacity="0.8"/>
        <stop offset="1" stop-color="#1d1f57" stop-opacity="0"/>
      </radialGradient>
      <radialGradient id="badge-fill" cx="0.4" cy="0.35" r="0.7">
        <stop offset="0" stop-color="#c8282d"/>
        <stop offset="1" stop-color="#8e1a1f"/>
      </radialGradient>
    </defs>
    <rect class="backdrop-decoration" x="0" y="0" width="800" height="460" fill="url(#wing-glow)" role="img" aria-label="Faint soaring eagle wing artwork behind the product name"/>
    <path class="swoosh-white" d="M0 393 C180 468 380 510 600 500 L800 412 L800 420 L600 512 C380 523 180 490 0 420 Z" fill="var(--white)"/>
    <path class="red-field" d="M0 440 C180 505 400 540 620 526 C700 518 760 482 800 440 L800 780 L0 780 Z" fill="var(--red)"/>
    <circle class="volume-badge" cx="659" cy="461" r="64" fill="url(#badge-fill)" stroke="var(--white)" stroke-width="6"/>

    <g class="pictogram pictogram-exclamation" transform="translate(620 584)">
      <rect x="-27" y="-27" width="54" height="54" transform="rotate(45)" fill="var(--white)" stroke="#d21f26" stroke-width="5"/>
      <rect x="-4" y="-20" width="8" height="26" rx="2" fill="var(--ink)"/>
      <circle cx="0" cy="14" r="4.5" fill="var(--ink)"/>
    </g>
    <g class="pictogram pictogram-health" transform="translate(712 584)">
      <rect x="-27" y="-27" width="54" height="54" transform="rotate(45)" fill="var(--white)" stroke="#d21f26" stroke-width="5"/>
      <circle cx="0" cy="-13" r="7" fill="var(--ink)"/>
      <path d="M-17 20 C-17 2 -10 -4 0 -4 C10 -4 17 2 17 20 Z" fill="var(--ink)"/>
      <path d="M0 1 L3 8 L10 9 L4 13 L6 20 L0 16 L-6 20 L-4 13 L-10 9 L-3 8 Z" fill="var(--white)"/>
    </g>
    <g class="pictogram pictogram-corrosive" transform="translate(620 679)">
      <rect x="-27" y="-27" width="54" height="54" transform="rotate(45)" fill="var(--white)" stroke="#d21f26" stroke-width="5"/>
      <rect x="-16" y="-18" width="7" height="13" transform="rotate(-20)" fill="var(--ink)"/>
      <rect x="6" y="-18" width="7" height="13" transform="rotate(20)" fill="var(--ink)"/>
      <rect x="-18" y="8" width="14" height="4" fill="var(--ink)"/>
      <rect x="2" y="10" width="18" height="5" fill="var(--ink)"/>
      <rect x="-22" y="17" width="44" height="4" fill="var(--ink)"/>
    </g>
    <g class="pictogram pictogram-flame" transform="translate(712 679)">
      <rect x="-27" y="-27" width="54" height="54" transform="rotate(45)" fill="var(--white)" stroke="#d21f26" stroke-width="5"/>
      <path d="M0 -22 C10 -10 14 -2 12 8 C10 14 5 16 0 16 C-7 16 -12 12 -12 4 C-12 -4 -6 -8 -4 -14 C-2 -8 2 -6 2 -2 C6 -8 4 -14 0 -22 Z" fill="var(--ink)"/>
      <rect x="-15" y="18" width="30" height="4" fill="var(--ink)"/>
    </g>
  </svg>

  <header class="brand">
    <span class="brand-mark" aria-hidden="true"></span>
    <span class="brand-name">Orvane<br>Thinner</span>
  </header>
  <p class="slogan">SOAR WITH PURPOSE</p>
  <h1 class="product-name">Thinner<br>QXR</h1>
  <p class="volume">4L</p>

  <section class="safety">
    <div class="safety-group">
      <div class="safety-item safety-title"><span class="num">1.</span><span>Precautionary Statements:</span></div>
      <div class="safety-item"><span class="num">1.</span><span>Keep Away from Sources of ignition - No Smoking</span></div>
      <div class="safety-item"><span class="num">2.</span><span>Avoid Contact with Eyes</span></div>
      <div class="safety-item"><span class="num">3.</span><span>Do Not Empty into Drains or Sewers</span></div>
      <div class="safety-item"><span class="num">4.</span><span>Take Precautionary Measures Against Static Discharge</span></div>
    </div>
    <div class="safety-group">
      <div class="safety-title">Hazard Statements:</div>
      <div class="safety-item"><span class="num">1.</span><span>Flammable Liquid and Vapor</span></div>
      <div class="safety-item"><span class="num">2.</span><span>May be fatal if swallowed or enters Airways</span></div>
      <div class="safety-item"><span class="num">3.</span><span>Causes Skin Irritation</span></div>
      <div class="safety-item"><span class="num">4.</span><span>Causes Serious Eye Irritation</span></div>
      <div class="safety-item"><span class="num">5.</span><span>Causes Damage to Organs if Prolonged or Repeated Exposure</span></div>
    </div>
  </section>
  <p class="signal-word">WARNING</p>
</main>
</body>
</html>
```